Awesome photographers card for an awesome new business

Double sided business card Black background and silver logo in middle on one side. Details on otherside. please keep it simple

Industry/Entity Type

Photographer

Contact Information for Business Card

Gerald Fenwick
0452817360
GeraldFenwickPhotography47@mailbox.test
www.GeraldFenwickPhotography.test.au
Instagram _Gerald_fenwick

Requirements
Must have
• My logo in Silver
• please use instagram logo instead of "Instagram"

```html
<!DOCTYPE html>
<html lang="en">
<head>
<meta charset="utf-8">
<title>Gerald Fenwick – Business Card</title>
<link rel="stylesheet" href="https://fonts.googleapis.com/css2?family=Lato:wght@400;700&display=swap">
<style>
  :root {
    --backdrop: #3a3a3b;
    --card: #262627;
    --silver: #cfcfcf;
    --silver-soft: #a9a9a9;
    --divider: #6a6a6a;
  }
  * { box-sizing: border-box; margin: 0; padding: 0; }
  html, body {
    width: 1200px;
    height: 880px;
    overflow: hidden;
    background: var(--backdrop);
    font-family: "Lato", Arial, sans-serif;
  }
  .canvas {
    width: 1200px;
    height: 880px;
    display: flex;
    flex-direction: column;
    align-items: center;
    justify-content: center;
    gap: 40px;
  }
  .card {
    width: 660px;
    height: 377px;
    background: var(--card);
    border-radius: 18px;
    box-shadow: 0 10px 30px rgba(0,0,0,0.45);
    position: relative;
  }
  .brand-mark {
    width: 170px;
    height: 170px;
    border: 3px solid var(--silver);
    border-radius: 50%;
    display: flex;
    align-items: center;
    justify-content: center;
    text-align: center;
    color: var(--silver);
    font-weight: 400;
    font-size: 22px;
    line-height: 1.25;
    letter-spacing: 0.04em;
  }
  .card--front {
    display: flex;
    align-items: center;
    justify-content: center;
  }
  .card--back {
    display: flex;
    align-items: center;
    padding-left: 40px;
  }
  .card--back .brand-mark {
    width: 150px;
    height: 150px;
    font-size: 19px;
  }
  .divider {
    width: 1px;
    height: 190px;
    background: var(--divider);
    margin: 0 26px 0 28px;
  }
  .details { color: var(--silver); }
  .details__name {
    font-weight: 700;
    font-size: 21px;
    letter-spacing: 0.02em;
    text-transform: uppercase;
    margin-bottom: 12px;
  }
  .contact-list { list-style: none; }
  .contact-list li {
    display: flex;
    align-items: center;
    gap: 8px;
    font-size: 15px;
    line-height: 22px;
  }
  .contact-icon {
    width: 15px;
    height: 15px;
    flex: none;
  }
  .details__web {
    font-size: 15px;
    margin-top: 12px;
  }
</style>
</head>
<body>
<main class="canvas">
  <section class="card card--front" aria-label="Card front">
    <div class="brand-mark">Gerald<br>Fenwick</div>
  </section>

  <section class="card card--back" aria-label="Card back">
    <div class="brand-mark">Gerald<br>Fenwick</div>
    <div class="divider"></div>
    <div class="details">
      <h1 class="details__name">Gerald Fenwick</h1>
      <ul class="contact-list">
        <li>
          <svg class="contact-icon" viewBox="0 0 16 16" aria-hidden="true">
            <circle cx="8" cy="8" r="7.5" fill="var(--silver)"/>
            <path d="M5 4.2c.4-.3.9-.2 1.1.2l.8 1.4c.2.4.1.8-.2 1.1l-.5.4c.4.9 1.1 1.6 2 2l.4-.5c.3-.3.7-.4 1.1-.2l1.4.8c.4.2.5.7.2 1.1l-.6.7c-.5.5-1.3.6-2 .3C6.8 10.6 5.4 9.2 4.5 7.3c-.3-.7-.2-1.5.3-2z" fill="var(--card)"/>
          </svg>
          0452817360
        </li>
        <li>
          <svg class="contact-icon" viewBox="0 0 16 16" aria-hidden="true">
            <circle cx="8" cy="8" r="7.5" fill="var(--silver)"/>
            <rect x="4" y="5" width="8" height="6" rx="0.8" fill="var(--card)"/>
            <path d="M4.3 5.4 8 8.3l3.7-2.9" stroke="var(--silver)" stroke-width="0.9" fill="none"/>
          </svg>
          GeraldFenwickPhotography47@mailbox.test
        </li>
        <li>
          <svg class="contact-icon" viewBox="0 0 16 16" aria-hidden="true">
            <circle cx="8" cy="8" r="7.5" fill="var(--silver)"/>
          </svg>
          Gerald_fenwick
        </li>
      </ul>
      <p class="details__web">www.GeraldFenwickPhotography.test.au</p>
    </div>
  </section>
</main>
</body>
</html>
```